BRINDLEWOOD EXTRA VIRGIN OLIVE OIL

I needs a design for an Australian Extra Virgin Olive Oil.

The label will go on a round clear bottle

The label size front and back is 145mm high x 60mm wide.

The important points for the design are as follows.

I want to see elegant olives on the label so that non English speaking markets can easily understand its olive oil. I want it too look classy . IT must also look Australian but I don't want to see kangaroos just colours that reflect Australia.

The mandatory info on front label will be

BRINDLEWOOD

Cold Pressed
EXTRA VIRGIN OLIVE OIL

AUSTRALIAN

1 litre

```html
<!DOCTYPE html>
<html lang="en">
<head>
<meta charset="utf-8">
<title>Brindlewood Extra Virgin Olive Oil – Label Options</title>
<link rel="stylesheet" href="https://fonts.googleapis.com/css2?family=Source+Sans+3:ital,wght@0,400;0,600;1,800&display=swap">
<style>
  :root {
    --page: #ffffff;
    --label-green: #28311f;
    --label-green-edge: #222a1a;
    --frame-gold: #f0a52a;
    --badge-gold: #c8912f;
    --text-light: #ffffff;
    --text-soft: #e9e9e4;
    --olive-dark: #3c4a1c;
    --olive-mid: #7d8b36;
    --olive-light: #cfd3a8;
    --shadow: rgba(0, 0, 0, 0.35);
  }
  * { box-sizing: border-box; margin: 0; padding: 0; }
  html, body {
    width: 1200px;
    height: 1089px;
    overflow: hidden;
    background: var(--page);
  }
  .canvas {
    position: relative;
    width: 1200px;
    height: 1089px;
    font-family: "Source Sans 3", "Helvetica Neue", Arial, sans-serif;
  }
  .label {
    position: absolute;
    top: 20px;
    width: 432px;
    height: 1025px;
    background: linear-gradient(160deg, var(--label-green) 0%, var(--label-green) 70%, var(--label-green-edge) 100%);
    border-radius: 26px;
    box-shadow: 8px 10px 14px var(--shadow);
    color: var(--text-light);
    text-align: center;
  }
  .label--classic { left: 62px; }
  .label--light { left: 716px; }

  .label__brand {
    position: absolute;
    top: 62px;
    left: 0;
    width: 100%;
    font-size: 27px;
    font-weight: 400;
    letter-spacing: 0.5px;
    color: var(--text-soft);
  }
  .label__photo-frame {
    position: absolute;
    top: 126px;
    left: 85px;
    width: 262px;
    height: 232px;
    border: 8px solid var(--frame-gold);
    background: var(--label-green);
  }
  .label__photo {
    width: 100%;
    height: 100%;
    background: radial-gradient(ellipse at 55% 60%, var(--olive-mid) 0%, var(--olive-dark) 55%, var(--label-green) 100%);
  }
  .label--classic .label__photo {
    background: radial-gradient(ellipse at 60% 65%, var(--olive-light) 0%, var(--olive-mid) 35%, var(--olive-dark) 75%, var(--label-green) 100%);
  }
  .label__grade {
    position: absolute;
    top: 405px;
    left: 0;
    width: 100%;
    font-size: 52px;
    font-weight: 400;
    line-height: 1;
    letter-spacing: 0.5px;
  }
  .label__product {
    position: absolute;
    top: 470px;
    left: 0;
    width: 100%;
    font-size: 56px;
    font-weight: 800;
    font-style: italic;
    line-height: 1;
    color: var(--text-soft);
    text-shadow: 2px 3px 2px rgba(0, 0, 0, 0.55);
  }
  .label__origin {
    position: absolute;
    top: 626px;
    left: 0;
    width: 100%;
    font-size: 27px;
    font-weight: 400;
    letter-spacing: 0.3px;
  }
  .label__method {
    position: absolute;
    top: 703px;
    left: 97px;
    width: 238px;
    height: 58px;
    background: var(--badge-gold);
    font-size: 27px;
    font-weight: 400;
    line-height: 58px;
  }
  .label__volume {
    position: absolute;
    right: 26px;
    bottom: 24px;
    font-size: 25px;
    font-weight: 400;
  }
</style>
</head>
<body>
<main class="canvas">

  <section class="label label--classic">
    <p class="label__brand">BRINDLEWOOD</p>
    <div class="label__photo-frame">
      <div class="label__photo" role="img" aria-label="Photograph of a sprig of olive leaves with a cluster of green and black olives"></div>
    </div>
    <h1 class="label__grade">EXTRA VIRGIN</h1>
    <h2 class="label__product">OLIVE OIL</h2>
    <p class="label__origin">AUSTRALIAN</p>
    <p class="label__method">Cold Pressed</p>
    <p class="label__volume">1 litre</p>
  </section>

  <section class="label label--light">
    <p class="label__brand">BRINDLEWOOD</p>
    <div class="label__photo-frame">
      <div class="label__photo" role="img" aria-label="Photograph of an olive branch with leaves and a few green olives"></div>
    </div>
    <h1 class="label__grade">EXTRA VIRGIN</h1>
    <h2 class="label__product">OLIVE OIL</h2>
    <p class="label__origin">AUSTRALIAN</p>
    <p class="label__method">Cold Pressed</p>
    <p class="label__volume">1 litre</p>
  </section>

</main>
</body>
</html>
```